KDWB Business Card

Looking for a business card design to incorporate our branding. We want to only use the colors listing in the Branding Package (attached).
Updates

Target Market(s)

People who need their phone or device fixed.

Industry/Entity Type

Electronics

Contact Information for Business Card

Please use:

Brightwick Gadget Clinic LLC
4810 E Harlow Ridge Rd
Suite 417
San Antonio, TX 78163

Marcus Delgrove, Store Manager

(210) 555-0147

Requirements
Must have
• Must include the colors that are contained within the Branding Package PDF file.

```html
<!DOCTYPE html>
<html lang="en">
<head>
<meta charset="utf-8">
<title>Brightwick Gadget Clinic – Business Card</title>
<link rel="stylesheet" href="https://fonts.googleapis.com/css2?family=Arimo:wght@400;500&display=swap">
<style>
  :root {
    --page-bg: #d9d9d7;
    --silver-light: #f4f3ef;
    --silver-mid: #d3d0c8;
    --silver-dark: #b9b5ac;
    --ink-black: #1c1c1d;
    --charcoal: #3a3a3c;
    --brand-red: #c8261c;
    --brand-red-bright: #e0452a;
    --text-dark: #141414;
    --text-light: #c9c4bb;
  }
  html, body {
    margin: 0;
    width: 1200px;
    height: 1200px;
    overflow: hidden;
    background: var(--page-bg);
    font-family: "Arimo", Arial, sans-serif;
  }
  .card {
    position: absolute;
    left: 50px;
    top: 270px;
    width: 1100px;
    height: 660px;
    overflow: hidden;
    box-shadow: 0 6px 18px rgba(0,0,0,0.25);
  }
  .card-art {
    position: absolute;
    inset: 0;
    width: 100%;
    height: 100%;
  }
  .brand {
    position: absolute;
    top: 140px;
    left: 0;
    width: 100%;
    display: flex;
    justify-content: center;
    align-items: center;
    gap: 20px;
  }
  .brand-square {
    width: 58px;
    height: 58px;
    border-radius: 10px;
    background: var(--brand-red);
  }
  .brand-name {
    font-size: 50px;
    font-weight: 400;
    color: var(--brand-red);
    letter-spacing: 0.5px;
  }
  .person {
    position: absolute;
    top: 312px;
    left: 0;
    width: 100%;
    text-align: center;
  }
  .person-name {
    font-size: 37px;
    color: var(--text-dark);
    letter-spacing: -0.5px;
    line-height: 1.1;
  }
  .person-title {
    font-size: 23px;
    color: var(--brand-red);
    letter-spacing: -0.3px;
    margin-top: 2px;
  }
  .contact {
    position: absolute;
    font-size: 26px;
    color: var(--text-light);
    letter-spacing: 0.6px;
    display: flex;
    align-items: center;
    gap: 10px;
  }
  .contact-phone { left: 78px; top: 488px; }
  .contact-email { right: 78px; top: 488px; }
  .contact-web { right: 78px; top: 528px; }
  .contact-address {
    left: 0;
    width: 100%;
    top: 590px;
    justify-content: center;
    font-size: 25px;
  }
  .icon {
    width: 26px;
    height: 26px;
    flex: none;
  }
</style>
</head>
<body>
  <div class="card">
    <svg class="card-art" viewBox="0 0 1100 660" preserveAspectRatio="none" aria-hidden="true">
      <defs>
        <linearGradient id="silverSheen" x1="0" y1="0" x2="1" y2="0.4">
          <stop offset="0" stop-color="var(--silver-mid)"/>
          <stop offset="0.3" stop-color="var(--silver-light)"/>
          <stop offset="0.55" stop-color="var(--silver-dark)"/>
          <stop offset="0.8" stop-color="var(--silver-light)"/>
          <stop offset="1" stop-color="var(--silver-mid)"/>
        </linearGradient>
        <linearGradient id="darkBase" x1="0" y1="0" x2="1" y2="0">
          <stop offset="0" stop-color="var(--ink-black)"/>
          <stop offset="0.3" stop-color="var(--charcoal)"/>
          <stop offset="0.6" stop-color="var(--ink-black)"/>
          <stop offset="1" stop-color="#111112"/>
        </linearGradient>
        <linearGradient id="redSwoosh" x1="0" y1="0" x2="1" y2="0">
          <stop offset="0" stop-color="var(--brand-red)"/>
          <stop offset="0.4" stop-color="var(--brand-red-bright)"/>
          <stop offset="1" stop-color="var(--brand-red)"/>
        </linearGradient>
      </defs>
      <rect class="silver-field" width="1100" height="660" fill="url(#silverSheen)"/>
      <path class="dark-base" d="M0,230 C150,430 360,478 570,475 C790,470 985,340 1100,134 L1100,660 L0,660 Z" fill="url(#darkBase)"/>
      <path class="red-swoosh" d="M0,103 C60,330 300,462 575,464 C760,464 900,350 970,276 C890,345 760,448 575,448 C340,450 95,330 0,155 Z" fill="url(#redSwoosh)"/>
    </svg>

    <div class="brand">
      <div class="brand-square"></div>
      <div class="brand-name">Brightwick Gadget Clinic</div>
    </div>

    <div class="person">
      <div class="person-name">Marcus Delgrove</div>
      <div class="person-title">Store Manager</div>
    </div>

    <div class="contact contact-phone">
      <svg class="icon" viewBox="0 0 26 26" aria-hidden="true">
        <rect width="26" height="26" fill="var(--text-light)"/>
        <path d="M8 5 L11 5 L12 9 L10 11 C11 14 12 16 15 17 L17 15 L21 16 L21 19 C21 20 20 21 19 21 C12 20 6 14 6 7 C6 6 7 5 8 5 Z" fill="var(--ink-black)"/>
      </svg>
      <span>(210) 555-0147</span>
    </div>

    <div class="contact contact-email">
      <span>marcus@BrightwickGadget.com</span>
      <svg class="icon" viewBox="0 0 26 26" aria-hidden="true">
        <rect width="26" height="26" fill="var(--text-light)"/>
        <rect x="5" y="8" width="16" height="11" fill="none" stroke="var(--ink-black)" stroke-width="1.8"/>
        <path d="M5 8 L13 15 L21 8" fill="none" stroke="var(--ink-black)" stroke-width="1.8"/>
      </svg>
    </div>

    <div class="contact contact-web">
      <span>www.BrightwickGadget.com</span>
      <svg class="icon" viewBox="0 0 26 26" aria-hidden="true">
        <rect width="26" height="26" fill="var(--text-light)"/>
        <circle cx="13" cy="13" r="8" fill="none" stroke="var(--ink-black)" stroke-width="1.8"/>
        <path d="M5 13 H21 M13 5 C9 9 9 17 13 21 M13 5 C17 9 17 17 13 21" fill="none" stroke="var(--ink-black)" stroke-width="1.4"/>
      </svg>
    </div>

    <div class="contact contact-address">4810 E Harlow Ridge Rd, Suite 417, San Antonio, TX 78163</div>
  </div>
</body>
</html>
```